Plakate für ein Fest
Zielgruppe
Das Kessner Park ist ein Gewerbepark mit unterschiedlichen Mietern von Handwerker über Musiker bis hin zu Vermögensberatung. Wir veranstalten ein Fest für unsere Mieter und möchten dieses Plakat als Einladung nutzen.
Aufgabenstellung
Hintergrund schwarz, Logo verwenden
Get together
BBQ & Cocktails im Kessner Park
am 13.10.2023 ab 18 Uhr
Logo Band wild pebbles
Kinderbereich
Wir freuen uns darauf, alle Mieter mit Familien begrüßen zu dürfen! Auch an die Kleinen haben wir gedacht.

```html
<!DOCTYPE html>
<html lang="de">
<head>
<meta charset="utf-8">
<title>Get Together – Kessner Park</title>
<link href="https://fonts.googleapis.com/css2?family=Roboto+Condensed:wght@300;500;600&family=Rubik+Dirt&display=swap" rel="stylesheet">
<style>
  :root {
    --bg: #151413;
    --ink: #ffffff;
    --accent: #3aa655;
    --glow-blue: #1b2250;
    --glow-pink: #a0306a;
    --glow-amber: #d0702a;
  }
  * { margin: 0; padding: 0; box-sizing: border-box; }
  html, body { width: 848px; height: 1200px; overflow: hidden; background: var(--bg); }
  .poster {
    position: relative;
    width: 848px;
    height: 1200px;
    background: radial-gradient(ellipse 70% 55% at 50% 55%, #0d0f1c 0%, var(--bg) 75%);
    color: var(--ink);
    font-family: "Roboto Condensed", "Arial Narrow", sans-serif;
  }
  .brand {
    position: absolute;
    top: 62px;
    left: 0;
    width: 100%;
    display: flex;
    justify-content: center;
    align-items: center;
    gap: 18px;
  }
  .brand-dot {
    width: 56px; height: 56px;
    border-radius: 50%;
    background: var(--accent);
  }
  .brand-name {
    font-weight: 600;
    font-size: 40px;
    line-height: 1;
    letter-spacing: 3px;
    text-transform: uppercase;
    color: var(--ink);
  }
  .cocktail-photo {
    position: absolute;
    left: 190px; top: 440px;
    width: 500px; height: 600px;
    background:
      radial-gradient(ellipse 38% 22% at 55% 22%, rgba(208,112,42,0.55) 0%, transparent 70%),
      radial-gradient(ellipse 45% 30% at 55% 28%, rgba(160,48,106,0.55) 0%, transparent 75%),
      radial-gradient(ellipse 60% 55% at 50% 45%, rgba(27,34,80,0.75) 0%, transparent 80%);
  }
  .headline {
    position: absolute;
    top: 196px;
    left: 0;
    width: 100%;
    text-align: center;
    font-family: "Rubik Dirt", Impact, sans-serif;
    font-size: 92px;
    line-height: 95px;
    letter-spacing: 2px;
    text-transform: uppercase;
  }
  .subline {
    position: absolute;
    top: 390px;
    left: 0;
    width: 100%;
    text-align: center;
    font-weight: 600;
    font-size: 46px;
    letter-spacing: 0.5px;
    text-transform: uppercase;
  }
  .event-info {
    position: absolute;
    left: 46px;
    top: 728px;
    font-weight: 600;
    font-size: 37px;
    line-height: 45px;
    text-transform: uppercase;
  }
  .band-name {
    position: absolute;
    left: 44px;
    top: 838px;
    font-weight: 600;
    font-size: 44px;
    letter-spacing: 2px;
    text-transform: uppercase;
  }
  .kids-area {
    position: absolute;
    left: 46px;
    top: 895px;
    font-weight: 600;
    font-size: 37px;
    text-transform: uppercase;
  }
  .invitation {
    position: absolute;
    top: 1084px;
    left: 0;
    width: 100%;
    text-align: center;
    font-weight: 300;
    font-size: 30px;
    line-height: 40px;
  }
</style>
</head>
<body>
  <main class="poster">
    <div class="cocktail-photo" role="img" aria-label="Foto: Martiniglas mit Olive, farbig beleuchtet, Flüssigkeit spritzt nach oben"></div>

    <header class="brand">
      <span class="brand-dot"></span>
      <span class="brand-name">Kessner Park</span>
    </header>

    <h1 class="headline">Get<br>Together</h1>
    <p class="subline">BBQ &amp; Cocktails im Kessner Park</p>

    <p class="event-info">Am 13.10.2023<br>ab 18 Uhr</p>
    <p class="band-name">wild pebbles</p>
    <p class="kids-area">Kinderbereich</p>

    <p class="invitation">Wir freuen uns darauf, alle Mieter mit Familien begrüßen<br>zu dürfen! Auch an die Kleinen haben wir gedacht.</p>
  </main>
</body>
</html>
```